Willow Landing - Multifamily Development

Willow Landing is a Luxury Multifamily Development project located in Orange, NJ. This project will be completed in three phases with the first phase about 75% complete. Each phase will have a different name as follows
CEDAR Willow Landing
LANTERN Willow Landing
BRAMBLEWOOD Willow Landing
We are going to install a banner on the side of the first building which will act as advertising for all buildings. We will eventually need advertising that will be in the windows as well as marketing materials . We want the marketing for this project to be similar for all three phases. At the moment, we are starting with this first simple banner. Attached is a rough idea of the look as well as our color palette. If you feel the color palette is a little too monochrome, feel free to propose an accent color. You can also visit our website to see more info on our company as well as the project. www.tarnlv.com Finally, if you need AI files (ie. for the logo), we can send to you. Thanks..

```html
<!DOCTYPE html>
<html lang="en">
<head>
<meta charset="utf-8">
<title>Willow Landing – Now Leasing Banner</title>
<link rel="stylesheet" href="https://fonts.googleapis.com/css2?family=Montserrat:wght@500&family=Oswald:wght@500;600&family=Poppins:ital,wght@0,800;1,800&display=swap">
<style>
  :root {
    --navy: #3f5170;
    --slate: #8799b2;
    --paper: #ffffff;
    --shadow: #c9d1dc;
    --ink-dark: #1f2a3d;
  }
  * { margin: 0; padding: 0; box-sizing: border-box; }
  html, body { width: 1200px; height: 456px; overflow: hidden; background: var(--navy); }
  .banner { position: relative; width: 1200px; height: 456px; background: var(--navy); }
  .panel { position: absolute; top: 76px; width: 250px; height: 303px; overflow: hidden; }
  .panel--name { left: 84px; background: var(--paper); }
  .panel--leasing { left: 345px; background: var(--slate); }
  .panel--contact { left: 607px; background: var(--paper); }
  .panel--brand { left: 868px; background: var(--slate); }

  .project-name {
    position: absolute; left: 128px; top: 152px;
    transform: translate(-50%, -50%) rotate(-90deg);
    font-family: "Montserrat", sans-serif; font-weight: 500;
    font-size: 37px; line-height: 33px; letter-spacing: 1px;
    color: var(--navy); white-space: nowrap;
    text-shadow: 2px 2px 0 var(--shadow);
  }
  .project-name span { display: block; }

  .headline {
    position: absolute; left: 44px; top: 98px;
    font-family: "Poppins", sans-serif; font-weight: 800; font-style: italic;
    font-size: 32px; line-height: 33px; color: var(--paper);
    text-shadow: 2px 2px 0 rgba(63, 81, 112, 0.35);
  }
  .headline span { display: block; }
  .headline .second { margin-left: -6px; }

  .lifestyle-art {
    position: absolute; left: 21px; top: 187px; width: 161px; height: 116px;
    background: linear-gradient(180deg, var(--slate) 0%, #5d6b84 45%, var(--ink-dark) 100%);
    border-radius: 40px 40px 0 0;
  }

  .contact-list { position: absolute; left: 36px; top: 104px; list-style: none;
    font-family: "Oswald", sans-serif; font-weight: 500; color: var(--navy); }
  .contact-list li { display: flex; align-items: center; gap: 8px; height: 22px; font-size: 14px; }
  .contact-list li.phone { height: 34px; font-size: 27px; font-weight: 600; }
  .contact-list svg { width: 14px; height: 14px; flex: none; }

  .tagline {
    position: absolute; left: 36px; top: 213px;
    font-family: "Poppins", sans-serif; font-weight: 800; font-style: italic;
    font-size: 19px; line-height: 21px; color: var(--navy);
    text-shadow: 1.5px 1.5px 0 var(--shadow);
  }
  .tagline span { display: block; }

  .company-name {
    position: absolute; left: 0; right: 0; top: 140px; text-align: center;
    font-family: "Poppins", sans-serif; font-weight: 800;
    font-size: 52px; line-height: 56px; letter-spacing: 1px; color: var(--paper);
  }
</style>
</head>
<body>
<main class="banner">
  <section class="panel panel--name">
    <h1 class="project-name"><span>WILLOW</span><span>LANDING</span></h1>
  </section>

  <section class="panel panel--leasing">
    <p class="headline"><span>NOW</span><span class="second">LEASING</span></p>
    <div class="lifestyle-art" role="img" aria-label="Illustration of a woman and child doing yoga poses beside an armchair, floor lamp and plants"></div>
  </section>

  <section class="panel panel--contact">
    <ul class="contact-list">
      <li>
        <svg viewBox="0 0 14 14" aria-hidden="true"><circle cx="7" cy="7" r="7" fill="#8799b2"/><path d="M7 3.2a2.4 2.4 0 0 0-2.4 2.4C4.6 7.4 7 10.6 7 10.6s2.4-3.2 2.4-5A2.4 2.4 0 0 0 7 3.2z" fill="#fff"/><circle cx="7" cy="5.6" r="0.9" fill="#8799b2"/></svg>
        CEDAR WILLOW LANDING
      </li>
      <li class="phone">
        <svg viewBox="0 0 14 14" aria-hidden="true"><circle cx="7" cy="7" r="7" fill="#8799b2"/><path d="M4.6 3.8l1.3-.3.7 1.7-.8.6a4.4 4.4 0 0 0 2.4 2.4l.6-.8 1.7.7-.3 1.3c-3 .2-5.8-2.6-5.6-5.6z" fill="#fff"/></svg>
        973.555.0148
      </li>
      <li>
        <svg viewBox="0 0 14 14" aria-hidden="true"><circle cx="7" cy="7" r="7" fill="#8799b2"/><rect x="3.6" y="4.6" width="6.8" height="4.8" fill="none" stroke="#fff" stroke-width="0.9"/><path d="M3.6 4.6L7 7.4l3.4-2.8" fill="none" stroke="#fff" stroke-width="0.9"/></svg>
        RENTALS@TARNLV.COM
      </li>
      <li>
        <svg viewBox="0 0 14 14" aria-hidden="true"><circle cx="7" cy="7" r="7" fill="#8799b2"/><path d="M5 3.6l4.6 4-2 .2 1.1 2.3-.8.4-1.1-2.3-1.6 1.3z" fill="#fff"/></svg>
        WWW.TARNLV.COM
      </li>
    </ul>
    <p class="tagline"><span>EXCEEDING</span><span>EXPECTATIONS</span></p>
  </section>

  <section class="panel panel--brand">
    <p class="company-name">TARN</p>
  </section>
</main>
</body>
</html>
```